Prosperity Pathway Basics PowerPoint

Please edit the following attached PowerPoint entitled workshop. Use the other attached PDF "TerraVesta Northern California Value Proposition" as a reference for the design and color I would like.

```html
<!DOCTYPE html>
<html lang="en">
<head>
<meta charset="utf-8">
<title>Prosperity Pathway Basics – Workshop Slides</title>
<link href="https://fonts.googleapis.com/css2?family=Poppins:wght@400;500;600&family=Lato:wght@400;700&display=swap" rel="stylesheet">
<style>
:root{
  --navy:#133f8e;
  --navy-deep:#0c2c69;
  --sky:#46c1ec;
  --ink:#2a2e39;
  --muted:#8a93a6;
  --paper:#f6f7fb;
  --page:#c8c8c8;
  --white:#ffffff;
}
*{box-sizing:border-box;margin:0;padding:0}
html,body{width:1026px;height:1200px;overflow:hidden}
body{background:var(--page);position:relative;font-family:"Lato",sans-serif;color:var(--ink)}
.slide{position:absolute;width:444px;height:250px;overflow:hidden;background:linear-gradient(135deg,#ffffff 0%,var(--paper) 60%,#eef1f8 100%)}
.slide.dark{background:var(--navy)}
.abs{position:absolute}
.scene{position:absolute;inset:0;background:radial-gradient(ellipse at 60% 35%,#2a57a6 0%,#17448f 45%,#0f3a84 100%);opacity:.9}
.title{position:absolute;left:25px;top:12px;font:500 13.5px/1 "Poppins",sans-serif;color:var(--navy);letter-spacing:.3px;white-space:nowrap}
.rule{position:absolute;left:0;top:37px;width:70px;height:1.3px;background:var(--sky)}
.rule::after{content:"";position:absolute;right:-3px;top:-3.3px;width:8px;height:8px;border-radius:50%;background:var(--sky)}
.foot{position:absolute;left:0;top:224px;width:300px;height:16px;background:var(--navy-deep);border-radius:0 8px 8px 0;display:flex;align-items:center;padding-left:25px;gap:4px;font:400 4.8px/1 "Lato",sans-serif;color:var(--white)}
.foot svg{width:5px;height:5px}
.foot .sep{margin:0 3px}
.foot .pg{position:absolute;right:3px;top:2.5px;width:11px;height:11px;border-radius:50%;background:var(--white);border:1px solid var(--navy-deep);color:var(--navy-deep);font:600 4.5px/9px "Poppins",sans-serif;text-align:center}
.dark .foot{background:var(--white);color:var(--navy-deep)}
.dark .foot .pg{background:var(--navy-deep);color:var(--white);border-color:var(--white)}
.brand{position:absolute;left:316px;top:220px;width:104px;text-align:center;color:var(--navy)}
.brand .name{display:flex;align-items:center;justify-content:center;gap:3px;font:600 14px/1 "Poppins",sans-serif}
.brand .name i{display:block;width:6px;height:6px;border-radius:50%;background:currentColor}
.brand .region{font:500 6.8px/1 "Poppins",sans-serif;margin-top:2px;padding-left:9px}
.dark .brand{color:var(--white)}
.small{font:400 5.3px/1.55 "Lato",sans-serif;color:var(--ink)}
.bullets{list-style:none}
.bullets li{position:relative;padding-left:7px}
.bullets li::before{content:"";position:absolute;left:0;top:50%;width:2px;height:2px;margin-top:-1px;border-radius:50%;background:var(--sky)}
.s1 .headline{left:25px;top:43px;font:600 21px/1 "Poppins",sans-serif;color:var(--white)}
.s1 .label{left:25px;font:500 12.5px/1 "Poppins",sans-serif;color:var(--white)}
.s1 .bullets{left:25px;font:400 7.4px/14px "Lato",sans-serif;color:var(--white)}
.s1 .bullets li{height:14px;padding-left:9px}
.s1 .closing{left:25px;top:181px;width:200px;font:400 9.2px/1.45 "Lato",sans-serif;color:var(--white)}
.s1 .brand{left:312px;top:12px}
.portrait{position:absolute;left:250px;top:30px;width:340px;height:340px;border-radius:50%;border:5px solid var(--sky);background:linear-gradient(140deg,#eef2f6 0%,#cfd8e3 45%,#8a97a8 100%)}
.s2 .photo{left:25px;top:56px;width:197px;height:152px;border-radius:12px;background:linear-gradient(135deg,#b8c7d8 0%,#5f7896 50%,#2f4666 100%)}
.s2 .copy{left:248px;top:70px;width:172px}
.s2 .copy p{margin-bottom:4px}
.s2 .sub{font:700 7px/1 "Lato",sans-serif;color:var(--navy);margin:8px 0 5px}
.s2 .bullets li{height:11px;line-height:11px}
.s3 .copy{left:25px;top:61px;width:206px;text-align:justify}
.s3 .copy .opts{font:700 6.4px/1.7 "Lato",sans-serif;color:var(--ink);margin:3px 0 2px;text-align:left}
.s3 .copy p{margin-bottom:3px}
.s3 .copy .fine{font-size:3.8px;line-height:1.65}
.petal{position:absolute;width:70px;height:70px;border-radius:50%;border:2px solid var(--white);box-shadow:0 1px 3px rgba(0,0,0,.25)}
.big{left:0;right:0;text-align:center;font:500 28px/1 "Poppins",sans-serif;color:var(--white);letter-spacing:.5px}
.contact-line{left:0;right:0;top:137px;display:flex;justify-content:center;align-items:center;gap:5px;font:400 8.8px/1 "Lato",sans-serif;color:var(--white)}
.contact-line svg{width:8px;height:8px}
.card{position:absolute;top:78px;width:124px;height:129px;border:1px solid #8fd6f2;border-radius:6px;background:var(--white);padding:24px 0 0 10px}
.card .badge{position:absolute;left:18px;top:-17px;width:33px;height:33px;border-radius:50%;background:var(--sky);display:flex;align-items:center;justify-content:center}
.card .badge svg{width:18px;height:18px}
.card h3{font:700 7px/1 "Lato",sans-serif;color:var(--navy);margin-bottom:6px}
.card .attr{font:700 4.8px/1 "Lato",sans-serif;color:var(--ink);margin:-1px 0 4px}
.card .bullets{font:400 5.4px/1 "Lato",sans-serif}
.card .bullets li{height:11px;line-height:11px;padding-left:12px}
.card .bullets li::before{left:1px}
.link-note{left:183px;width:80px;text-align:center;font:400 5.3px/1.5 "Lato",sans-serif;color:var(--ink)}
.s6 .copy{left:42px;top:67px;width:360px;text-align:center;font:400 7.2px/1.5 "Lato",sans-serif;color:var(--ink)}
.s6 .copy p{margin-bottom:6px}
.s7 .copy{left:296px;top:96px;width:123px;text-align:justify;font:400 7px/1.38 "Lato",sans-serif;color:var(--ink)}
</style>
</head>
<body>

<section class="slide dark s1" style="left:51px;top:54px">
  <div class="scene" role="img" aria-label="Blue-toned view of a suspension bridge over the bay"></div>
  <div class="portrait" role="img" aria-label="Advisor meeting a client across a desk"></div>
  <div class="brand"><div class="name"><i></i>TerraVesta</div><div class="region">Northern California</div></div>
  <h1 class="abs headline">YOUR MONEY</h1>
  <h2 class="abs label" style="top:72px">OBJECTIVE:</h2>
  <ul class="abs bullets" style="top:90px"><li>Build as big as possible</li></ul>
  <h2 class="abs label" style="top:111px">HOW:</h2>
  <ul class="abs bullets" style="top:129px"><li>Higher rates of return?</li><li>More risk?</li><li>"Better" products?</li></ul>
  <p class="abs closing">Having an efficient overall strategy is the key; it all starts here!</p>
</section>

<section class="slide s2" style="left:532px;top:54px">
  <h2 class="title">WHY IS YOUR STRATEGY SO IMPORTANT?</h2>
  <div class="rule"></div>
  <div class="abs photo" role="img" aria-label="Team of advisors reviewing work around a laptop"></div>
  <div class="abs copy small">
    <p>We all only have a finite amount of money...we have to be efficient with it in the short time we have.</p>
    <p>Inefficiencies cause major losses to occur.</p>
    <div class="sub">THESE LOSSES CAN BE REFLECTED IN:</div>
    <ul class="bullets">
      <li>Lower current lifestyle</li><li>Lower retirement income</li><li>Inadequate protection</li><li>Loss of financial control</li><li>Financial vulnerability</li><li>Higher taxes and fees</li><li>Less benefits</li>
    </ul>
  </div>
  <div class="foot"><svg viewBox="0 0 10 10"><path d="M2 1l2 0 1 2.5-1.3 1a6 6 0 0 0 2.8 2.8l1-1.3L10 7v2a1 1 0 0 1-1 1A9 9 0 0 1 0 1a1 1 0 0 1 1-1z" fill="var(--sky)"/></svg>925-555-0148<span class="sep">|</span><svg viewBox="0 0 10 10"><circle cx="5" cy="5" r="4.5" fill="var(--sky)"/></svg>https://northerncalifornia.terravesta.com/<span class="pg">02</span></div>
  <div class="brand"><div class="name"><i></i>TerraVesta</div><div class="region">Northern California</div></div>
</section>

<section class="slide s3" style="left:51px;top:335px">
  <h2 class="title">TWIN INCOME LEVERS APPROACH</h2>
  <div class="rule"></div>
  <div class="abs copy small">
    <p>When we reach retirement there are 2 global options for generating retirement income streams from the assets we've built:</p>
    <div class="opts">1. Exchange/Trade your money<br>2. Invest your money</div>
    <p>If we don't incorporate Actuarial Science we can be relegating/defaulting ourselves to the 3-4% income rate problem. When we incorporate Actuarial Science along the way we put ourselves on a path that can potentially provide higher retirement income rates from the assets we've built. The balancing between these income levers (Cornerstones) is the key... Having too much of either can make you less efficient.</p>
    <p>When you balance the income levers (Cornerstones) along the way you get both retirement income options: 1) Exchanging/Trading (Covered Assets) or 2) Investing (Volatility Buffer) to choose from or combine together at retirement time to potentially provide higher overall retirement income.</p>
    <p class="fine">Guarantees occur at the time a product is purchased that provides those guarantees, and at that time the guarantees are based on the claims paying ability of the issuing company. Guarantees do not apply to investment performance or account values. Past performance is no guarantee of future results.</p>
  </div>
  <div class="petal" style="left:298px;top:47px;background:linear-gradient(135deg,#dfe6ef,#7f96b4)" role="img" aria-label="Hands reviewing financial charts"></div>
  <div class="petal" style="left:247px;top:98px;background:linear-gradient(135deg,#e9edf2,#5c7393)" role="img" aria-label="Colleagues meeting at a laptop"></div>
  <div class="petal" style="left:349px;top:98px;background:linear-gradient(135deg,#f1e3b8,#7e93b0)" role="img" aria-label="Calculator and paperwork on a desk"></div>
  <div class="petal" style="left:298px;top:146px;background:linear-gradient(135deg,#eef1f5,#43597a)" role="img" aria-label="Presenter speaking to a small team"></div>
  <div class="foot"><svg viewBox="0 0 10 10"><path d="M2 1l2 0 1 2.5-1.3 1a6 6 0 0 0 2.8 2.8l1-1.3L10 7v2a1 1 0 0 1-1 1A9 9 0 0 1 0 1a1 1 0 0 1 1-1z" fill="var(--sky)"/></svg>925-555-0148<span class="sep">|</span><svg viewBox="0 0 10 10"><circle cx="5" cy="5" r="4.5" fill="var(--sky)"/></svg>https://northerncalifornia.terravesta.com/<span class="pg">03</span></div>
  <div class="brand"><div class="name"><i></i>TerraVesta</div><div class="region">Northern California</div></div>
</section>

<section class="slide dark" style="left:532px;top:335px">
  <div class="scene" role="img" aria-label="Blue-toned view of a suspension bridge over the bay"></div>
  <h2 class="abs big" style="top:109px">SECTION DIVIDER</h2>
  <div class="foot"><svg viewBox="0 0 10 10"><path d="M2 1l2 0 1 2.5-1.3 1a6 6 0 0 0 2.8 2.8l1-1.3L10 7v2a1 1 0 0 1-1 1A9 9 0 0 1 0 1a1 1 0 0 1 1-1z" fill="var(--sky)"/></svg>925-555-0148<span class="sep">|</span><svg viewBox="0 0 10 10"><circle cx="5" cy="5" r="4.5" fill="var(--sky)"/></svg>https://northerncalifornia.terravesta.com/<span class="pg">04</span></div>
  <div class="brand"><div class="name"><i></i>TerraVesta</div><div class="region">Northern California</div></div>
</section>

<section class="slide s5" style="left:51px;top:616px">
  <h2 class="title">LONG TERM WEALTH BUILDING</h2>
  <div class="rule"></div>
  <div class="card" style="left:58px">
    <div class="badge"><svg viewBox="0 0 20 20" fill="none" stroke="#fff" stroke-width="1.3"><circle cx="8" cy="11" r="5.5"/><path d="M8 8v6M6.5 9.5h2.5a1 1 0 0 1 0 2H7a1 1 0 0 0 0 2h2.5"/><path d="M14 3l3 1.2v3c0 2-1.4 3.2-3 3.8-1.6-.6-3-1.8-3-3.8v-3z"/></svg></div>
    <h3>RETIREMENT ASSETS</h3>
    <ul class="bullets"><li>401k/IRAs/403b</li><li>Growth Securities/Stocks/Bonds</li><li>CD's</li><li>Annuities</li><li>Universal Life Insurance</li><li>Real Estate</li><li>Businesses, Etc.</li></ul>
  </div>
  <div class="abs link-note" style="top:110px;font-size:4.9px">UNCORRELATED</div>
  <svg class="abs" style="left:190px;top:123px" width="66" height="16" viewBox="0 0 66 16"><path d="M0 8l9-7v4.5h48V1l9 7-9 7v-4.5H9V15z" fill="var(--navy-deep)"/></svg>
  <div class="abs link-note" style="top:144px">Different<br>Characteristics</div>
  <div class="card" style="left:261px">
    <div class="badge"><svg viewBox="0 0 20 20" fill="none" stroke="#fff" stroke-width="1.3"><path d="M10 2l5 2v4c0 3-2.2 5-5 6-2.8-1-5-3-5-6V4z"/><path d="M7.6 8l1.7 1.7L12.6 6.5"/><path d="M2 13c2 0 3 2 5 3h3M18 13c-2 0-3 2-5 3h-3"/></svg></div>
    <h3>WHOLE LIFE INSURANCE</h3>
    <div class="attr">ATTRIBUTES INCLUDE:</div>
    <ul class="bullets"><li>Permanent Death Benefit</li><li>Cash Values</li><li>Dividends</li><li>Loans</li><li>Disability Protection of Premium</li><li>Etc.</li></ul>
  </div>
  <div class="foot"><svg viewBox="0 0 10 10"><path d="M2 1l2 0 1 2.5-1.3 1a6 6 0 0 0 2.8 2.8l1-1.3L10 7v2a1 1 0 0 1-1 1A9 9 0 0 1 0 1a1 1 0 0 1 1-1z" fill="var(--sky)"/></svg>925-555-0148<span class="sep">|</span><svg viewBox="0 0 10 10"><circle cx="5" cy="5" r="4.5" fill="var(--sky)"/></svg>https://northerncalifornia.terravesta.com/<span class="pg">05</span></div>
  <div class="brand"><div class="name"><i></i>TerraVesta</div><div class="region">Northern California</div></div>
</section>

<section class="slide s6" style="left:532px;top:616px">
  <h2 class="title">OPTION #1 – COVERED RETIREMENT ASSETS</h2>
  <div class="rule"></div>
  <div class="abs copy">
    <p>A Covered Retirement Asset is one that is accompanied by an equal amount of Whole Life Death Benefit. Similar to how most government entities provide retirement pensions to their employees, Covered Retirement Assets lay the foundation for self-made pensions in retirement.</p>
    <p>This is accomplished through the interaction of a retirement income tool that is unrelated to the curves of the withdrawal rate simulations called an income annuity (self-made pension) and your Whole Life Death Benefit.</p>
    <p>Basically under this option the interaction of your Retirement Assets and Whole Life Death Benefit gives you the ability to create guaranteed retirement income for life historically in the range of 7-13% from the assets you've built, while at the same time providing perpetuation of retirement income for a spouse and/or a legacy for your heirs. The closer you get to having the same amount of Retirement Assets and Whole Life Death Benefit at retirement time the more Covered Assets you have and the higher your retirement income can go.</p>
  </div>
  <div class="foot"><svg viewBox="0 0 10 10"><path d="M2 1l2 0 1 2.5-1.3 1a6 6 0 0 0 2.8 2.8l1-1.3L10 7v2a1 1 0 0 1-1 1A9 9 0 0 1 0 1a1 1 0 0 1 1-1z" fill="var(--sky)"/></svg>925-555-0148<span class="sep">|</span><svg viewBox="0 0 10 10"><circle cx="5" cy="5" r="4.5" fill="var(--sky)"/></svg>https://northerncalifornia.terravesta.com/<span class="pg">06</span></div>
  <div class="brand"><div class="name"><i></i>TerraVesta</div><div class="region">Northern California</div></div>
</section>

<section class="slide s7" style="left:51px;top:897px">
  <h2 class="title">TIME IS OF THE ESSENCE</h2>
  <div class="rule"></div>
  <svg class="abs" style="left:0;top:0" width="444" height="250" viewBox="0 0 444 250" font-family="Lato, sans-serif">
    <g fill="var(--ink)" font-size="4.8" font-weight="700" text-anchor="end">
      <text x="51" y="61.5">$3,500,000</text><text x="51" y="80.6">$3,000,000</text><text x="51" y="104.3">$2,500,000</text><text x="51" y="128.1">$1,500,000</text><text x="51" y="151.8">$1,000,000</text><text x="51" y="170.8">$500,000</text><text x="51" y="194.8">$0</text>
    </g>
    <g stroke="#dde1ea" stroke-width=".5">
      <line x1="55" y1="60" x2="278" y2="60"/><line x1="55" y1="200" x2="278" y2="200"/>
      <line x1="55" y1="60" x2="55" y2="200"/><line x1="86.9" y1="60" x2="86.9" y2="200"/><line x1="118.8" y1="60" x2="118.8" y2="200"/><line x1="150.7" y1="60" x2="150.7" y2="200"/><line x1="182.6" y1="60" x2="182.6" y2="200"/><line x1="214.5" y1="60" x2="214.5" y2="200"/><line x1="246.4" y1="60" x2="246.4" y2="200"/><line x1="278" y1="60" x2="278" y2="200"/>
    </g>
    <g fill="var(--navy-deep)">
      <rect x="63" y="84" width="5.5" height="116"/><rect x="94.9" y="95.6" width="5.5" height="104.4"/><rect x="126.8" y="142" width="5.5" height="58"/><rect x="158.7" y="84" width="5.5" height="116"/><rect x="190.6" y="84" width="5.5" height="116"/><rect x="222.5" y="130.4" width="5.5" height="69.6"/><rect x="254.4" y="142" width="5.5" height="58"/>
    </g>
    <g fill="var(--sky)">
      <rect x="72" y="95.6" width="5.5" height="104.4"/><rect x="103.9" y="107.2" width="5.5" height="92.8"/><rect x="135.8" y="84" width="5.5" height="116"/><rect x="167.7" y="130.4" width="5.5" height="69.6"/><rect x="199.6" y="95.6" width="5.5" height="104.4"/><rect x="231.5" y="113" width="5.5" height="87"/><rect x="263.4" y="84" width="5.5" height="116"/>
    </g>
    <g fill="var(--ink)" font-size="4.8" text-anchor="middle">
      <text x="65.8" y="81">100</text><text x="74.8" y="92.6">90</text>
      <text x="97.7" y="92.6">90</text><text x="106.7" y="104.2">80</text>
      <text x="129.6" y="139">50</text><text x="138.6" y="81">100</text>
      <text x="161.5" y="81">100</text><text x="170.5" y="127.4">60</text>
      <text x="193.4" y="81">100</text><text x="202.4" y="92.6">90</text>
      <text x="225.3" y="127.4">60</text><text x="234.3" y="110">75</text>
      <text x="257.2" y="139">50</text><text x="266.2" y="81">100</text>
    </g>
    <g fill="var(--ink)" font-size="4.8" font-weight="700" text-anchor="middle">
      <text x="71" y="208">Sun</text><text x="102.9" y="208">Mon</text><text x="134.8" y="208">Tue</text><text x="166.7" y="208">Wed</text><text x="198.6" y="208">Thu</text><text x="230.5" y="208">Fri</text><text x="262.4" y="208">Sat</text>
    </g>
  </svg>
  <p class="abs copy">It is imperative to implement efficient wealth building strategies beginning with the end in mind as soon as possible. The longer you wait the more wealth opportunity comes off the back end of the curve, and this is when the majority of wealth is created.</p>
  <div class="foot"><svg viewBox="0 0 10 10"><path d="M2 1l2 0 1 2.5-1.3 1a6 6 0 0 0 2.8 2.8l1-1.3L10 7v2a1 1 0 0 1-1 1A9 9 0 0 1 0 1a1 1 0 0 1 1-1z" fill="var(--sky)"/></svg>925-555-0148<span class="sep">|</span><svg viewBox="0 0 10 10"><circle cx="5" cy="5" r="4.5" fill="var(--sky)"/></svg>https://northerncalifornia.terravesta.com/<span class="pg">07</span></div>
  <div class="brand"><div class="name"><i></i>TerraVesta</div><div class="region">Northern California</div></div>
</section>

<section class="slide dark" style="left:532px;top:897px">
  <div class="scene" role="img" aria-label="Blue-toned view of a suspension bridge over the bay"></div>
  <div class="brand" style="top:19px"><div class="name"><i></i>TerraVesta</div><div class="region">Northern California</div></div>
  <h2 class="abs big" style="top:99px;font-size:29px">THANK YOU</h2>
  <div class="abs contact-line">
    <svg viewBox="0 0 10 10"><path d="M2 1l2 0 1 2.5-1.3 1a6 6 0 0 0 2.8 2.8l1-1.3L10 7v2a1 1 0 0 1-1 1A9 9 0 0 1 0 1a1 1 0 0 1 1-1z" fill="var(--sky)"/></svg>
    <span>925-555-0148</span><span style="margin:0 4px">|</span>
    <svg viewBox="0 0 10 10"><circle cx="5" cy="5" r="4.5" fill="var(--sky)"/></svg>
    <span>https://northerncalifornia.terravesta.com/</span>
  </div>
</section>

</body>
</html>
```